Residential Remodeling Contractor needs updated business card

I need a new design for my business card.
Name of the company is Ridgefell Construction. I need a card that commands presence, strength, integrity. I have been in business for 28 years. I am a Residential Remodeling Contractor that covers all aspects of a residential remodel and build.

```html
<!DOCTYPE html>
<html lang="en">
<head>
<meta charset="utf-8">
<title>Ridgefell Construction — Business Card</title>
<link href="https://fonts.googleapis.com/css2?family=Libre+Baskerville:wght@700&family=Arimo:wght@400&display=swap" rel="stylesheet">
<style>
  :root {
    --backdrop: #9a9a9a;
    --navy: #1a3e7b;
    --navy-back: #223b7e;
    --pattern-light: #6f8fc6;
    --white: #ffffff;
    --title-grey: #444444;
  }
  * { margin: 0; padding: 0; box-sizing: border-box; }
  html, body { width: 1200px; height: 1059px; overflow: hidden; }
  body { background: var(--backdrop); position: relative; font-family: "Arimo", Arial, sans-serif; }

  .card { position: absolute; width: 690px; height: 392px; border-radius: 15px; overflow: hidden; }
  .card-front { left: 255px; top: 89px; background: var(--white); }
  .card-back { left: 255px; top: 569px; background: var(--navy-back); }

  .wave { position: absolute; inset: 0; width: 100%; height: 100%; }

  .brand { position: absolute; display: flex; align-items: center; gap: 14px;
           font-family: "Libre Baskerville", Georgia, serif; font-weight: 700; line-height: 1.08; }
  .brand-mark { width: 16px; height: 16px; flex: none; }
  .brand-name { font-size: 30px; letter-spacing: 0.5px; }
  .card-front .brand { left: 42px; top: 78px; color: var(--navy); }
  .card-front .brand-mark { background: var(--navy); }
  .card-back .brand { left: 452px; top: 282px; color: var(--white); gap: 10px; }
  .card-back .brand-name { font-size: 21px; }
  .card-back .brand-mark { background: var(--white); width: 12px; height: 12px; }

  .holder { position: absolute; right: 30px; top: 82px; text-align: right; }
  .holder-name { font-family: "Libre Baskerville", Georgia, serif; font-weight: 700; font-size: 23px;
                 color: var(--navy); letter-spacing: 0.3px; line-height: 1; }
  .holder-title { font-size: 16px; color: var(--title-grey); margin-top: 4px; }

  .address { position: absolute; right: 30px; top: 204px; text-align: right; color: var(--white);
             font-size: 16px; line-height: 21px; }

  .contacts { position: absolute; right: 26px; top: 266px; list-style: none; color: var(--white);
              font-size: 16px; }
  .contacts li { display: flex; justify-content: flex-end; align-items: center; gap: 9px; height: 24.3px; }
  .contacts svg { width: 13px; height: 13px; flex: none; }

  .pattern-field { position: absolute; inset: 0;
    background: linear-gradient(100deg, var(--navy-back) 0%, #2a4588 45%, var(--pattern-light) 100%);
    -webkit-mask: linear-gradient(to bottom, #000 0%, #000 60%, rgba(0,0,0,0.35) 100%);
            mask: linear-gradient(to bottom, #000 0%, #000 60%, rgba(0,0,0,0.35) 100%); }
</style>
</head>
<body>

<section class="card card-front" aria-label="Business card front">
  <svg class="wave" viewBox="0 0 690 392" preserveAspectRatio="none" aria-hidden="true">
    <defs>
      <linearGradient id="swoosh-fade" x1="0" y1="0" x2="1" y2="0">
        <stop offset="0" stop-color="#1a3e7b" stop-opacity="0.15"/>
        <stop offset="0.12" stop-color="#1a3e7b"/>
        <stop offset="0.8" stop-color="#1a3e7b"/>
        <stop offset="1" stop-color="#1a3e7b" stop-opacity="0"/>
      </linearGradient>
    </defs>
    <path d="M0,246 C45,285 110,308 190,303 C320,294 450,150 575,138 C625,134 662,152 690,172"
          fill="none" stroke="url(#swoosh-fade)" stroke-width="13"/>
    <path d="M0,273 C50,306 120,322 205,312 C335,295 460,168 578,155 C628,150 664,168 690,188 L690,392 L0,392 Z"
          fill="#1a3e7b"/>
  </svg>

  <div class="brand">
    <span class="brand-mark"></span>
    <span class="brand-name">Ridgefell<br>Construction</span>
  </div>

  <div class="holder">
    <p class="holder-name">DANIEL WHITCOMBE</p>
    <p class="holder-title">Owner &amp; Manager</p>
  </div>

  <p class="address">P.O. Box&nbsp; Street Name<br>Country Name AB, A5B 521</p>

  <ul class="contacts">
    <li>555 214 7730
      <svg viewBox="0 0 16 16" aria-hidden="true"><path fill="#fff" d="M1 6c0-2 3-3 7-3s7 1 7 3v1h-3V5.5H4V7H1z M3 8h10l1 6H2z"/></svg>
    </li>
    <li>555-318-60427
      <svg viewBox="0 0 16 16" aria-hidden="true"><rect x="4" y="1" width="8" height="14" rx="1.5" fill="none" stroke="#fff" stroke-width="1.6"/><circle cx="8" cy="12.5" r="0.9" fill="#fff"/></svg>
    </li>
    <li>info@ridgefellconstruction.com
      <svg viewBox="0 0 16 16" aria-hidden="true"><path fill="#fff" d="M1 7l7-5 7 5v8H1z"/><path d="M1 7l7 5 7-5" fill="none" stroke="#1a3e7b" stroke-width="1.2"/></svg>
    </li>
    <li>www.ridgefellconstruction.com
      <svg viewBox="0 0 16 16" aria-hidden="true"><circle cx="8" cy="8" r="7" fill="#fff"/><path fill="#1a3e7b" d="M5 4l3 1 1 3-3 1-1 3-2-3zM10 10l3-1-1 4z"/></svg>
    </li>
  </ul>
</section>

<section class="card card-back" aria-label="Business card back">
  <div class="pattern-field" role="img" aria-label="Repeating brand pattern fading from dark navy to light blue"></div>
  <div class="brand">
    <span class="brand-mark"></span>
    <span class="brand-name">Ridgefell<br>Construction</span>
  </div>
</section>

</body>
</html>
```